Business Card Design

New business card design

Target Market(s)

Residential & Commercial Property Managers

Industry/Entity Type

Plumbing Services

Contact Information for Business Card

Name - Rowan Keddle, title - Director, Phone Number - 0431 286 517, email - rowan@tbk-plumbing.com.au, Company ABN - 73 215 904 386,

Font styles to use
Sans Serif

Colors
0054AA
0677BA
7BADD7
CADEEF
E8F1F8

```html
<!DOCTYPE html>
<html lang="en">
<head>
<meta charset="utf-8">
<title>TBK Plumbing Services – Business Cards</title>
<link rel="stylesheet" href="https://fonts.googleapis.com/css2?family=Poppins:wght@300;400;500;600&display=swap">
<style>
  :root {
    --backdrop: #222324;
    --card: #1b222a;
    --card-edge: #141a20;
    --white: #ffffff;
    --blue: #2aa3dc;
    --blue-line: #1f86bf;
    --taupe: #7d7166;
    --muted: #8d96a0;
  }
  * { margin: 0; padding: 0; box-sizing: border-box; }
  html, body {
    width: 1200px; height: 780px; overflow: hidden;
    background: var(--backdrop);
    font-family: "Poppins", sans-serif;
  }
  .canvas {
    position: relative; width: 1200px; height: 780px;
    display: flex; align-items: center; justify-content: center; gap: 48px;
  }
  .card {
    position: relative; width: 520px; height: 318px;
    background: var(--card);
    box-shadow: 0 2px 0 var(--card-edge), 0 18px 40px rgba(0,0,0,.45);
    overflow: hidden;
  }
  /* brand name set as plain text */
  .brand {
    display: flex; align-items: center; gap: 12px;
    color: var(--white); font-weight: 300; letter-spacing: .06em;
    white-space: nowrap;
  }
  .brand-dot { border-radius: 50%; background: var(--blue); flex: none; }
  .card-front .brand {
    position: absolute; left: 0; right: 0; top: 0; bottom: 0;
    justify-content: center; font-size: 30px;
  }
  .card-front .brand-dot { width: 18px; height: 18px; }

  .card-back .brand {
    position: absolute; left: 34px; top: 70px; font-size: 17px;
  }
  .card-back .brand-dot { width: 11px; height: 11px; }
  .divider { position: absolute; left: 0; top: 0; }
  .person { position: absolute; left: 282px; top: 96px; }
  .person-name { font-size: 26px; line-height: 1.1; white-space: nowrap; }
  .first-name { color: var(--blue); font-weight: 600; }
  .last-name { color: var(--taupe); font-weight: 300; }
  .person-title { color: var(--white); font-size: 13px; font-weight: 500; margin-top: 2px; }
  .contacts { list-style: none; margin-top: 16px; }
  .contacts li {
    display: flex; align-items: center; gap: 9px;
    color: var(--white); font-size: 12.5px; font-weight: 400; line-height: 22px;
  }
  .contacts svg { width: 13px; height: 13px; flex: none; }
  .abn {
    position: absolute; left: 34px; bottom: 36px;
    color: var(--blue); font-size: 12.5px; font-weight: 400;
  }
</style>
</head>
<body>
<main class="canvas">
  <section class="card card-back" aria-label="Business card, contact side">
    <div class="brand"><span class="brand-dot"></span>TBK Plumbing Services</div>
    <svg class="divider" width="520" height="318" aria-hidden="true">
      <line x1="205" y1="272" x2="262" y2="60" stroke="var(--blue-line)" stroke-width="1"/>
    </svg>
    <div class="person">
      <div class="person-name"><span class="first-name">Rowan</span> <span class="last-name">Keddle</span></div>
      <div class="person-title">Director</div>
      <ul class="contacts">
        <li>
          <svg viewBox="0 0 24 24" aria-hidden="true"><path fill="var(--blue)" d="M6.6 10.8a15.1 15.1 0 0 0 6.6 6.6l2.2-2.2a1 1 0 0 1 1-.25 11.4 11.4 0 0 0 3.6.57 1 1 0 0 1 1 1V20a1 1 0 0 1-1 1A17 17 0 0 1 3 4a1 1 0 0 1 1-1h3.5a1 1 0 0 1 1 1c0 1.25.2 2.45.57 3.57a1 1 0 0 1-.25 1z"/></svg>
          0431 286 517
        </li>
        <li>
          <svg viewBox="0 0 24 24" aria-hidden="true"><rect x="2" y="5" width="20" height="14" rx="2" fill="var(--blue)"/><path d="M3 6.5l9 6.5 9-6.5" fill="none" stroke="var(--card)" stroke-width="1.8"/></svg>
          rowan@tbk-plumbing.com.au
        </li>
        <li>
          <svg viewBox="0 0 24 24" aria-hidden="true"><circle cx="12" cy="12" r="10" fill="var(--blue)"/><path d="M2 12h20M12 2c3 3 3 17 0 20M12 2c-3 3-3 17 0 20" fill="none" stroke="var(--card)" stroke-width="1.4"/></svg>
          www.tbk-plumbing.com.au
        </li>
      </ul>
    </div>
    <p class="abn">ABN - 73 215 904 386,</p>
  </section>

  <section class="card card-front" aria-label="Business card, brand side">
    <div class="brand"><span class="brand-dot"></span>TBK Plumbing Services</div>
  </section>
</main>
</body>
</html>
```